Looking for someone to design a business card for my plumbing business Quandor Plumbing Solutions I want the background also to be black, must attract clients. If possible I want the front to be the logo and the back to show maybe the details.

Target Market(s)

Clients

Industry/Entity Type

Plumbing maintenance

Contact Information for Business Card

Name: Felix, Contact: 0461 539 207, Email: quandorplumbingsolutions@mailbrook.example, Licence number 728093K

Font styles to use
Other font styles liked:
• as per logo maybe?

Colors

Designer to choose colors to be used in the design.

Requirements
Nice to have
• stating the service I provide, emergency plumbing, plumbing maintenance, drainage maintenance, block sewer and stormwater, camera and locating.

```html
<!DOCTYPE html>
<html lang="en">
<head>
<meta charset="UTF-8">
<title>Quandor Plumbing Solutions – Business Card</title>
<link rel="stylesheet" href="https://fonts.googleapis.com/css2?family=Montserrat:wght@400;500;800&display=swap">
<style>
  :root {
    --backdrop: #c9c9c7;
    --card: #1f1f20;
    --accent: #4a90d9;
    --ink: #f2f2f2;
    --ink-soft: #d9d9d9;
    --logo-muted: #4a4a4c;
  }
  * { box-sizing: border-box; margin: 0; padding: 0; }
  html, body { width: 1200px; height: 801px; overflow: hidden; }
  body {
    background: var(--backdrop);
    font-family: "Montserrat", sans-serif;
    display: flex;
    align-items: center;
    justify-content: center;
    gap: 40px;
  }
  .card {
    position: relative;
    width: 540px;
    height: 330px;
    background: var(--card);
    border-left: 4px solid var(--accent);
    border-bottom: 4px solid var(--accent);
    box-shadow: 0 14px 30px rgba(0,0,0,0.28);
    overflow: hidden;
  }

  /* Details side */
  .brand {
    position: absolute;
    left: 36px;
    top: 40px;
    display: flex;
    align-items: center;
    gap: 10px;
  }
  .brand-dot {
    width: 30px; height: 30px;
    border-radius: 50%;
    background: var(--ink);
  }
  .brand-name {
    color: var(--ink);
    font-weight: 800;
    font-size: 17px;
    text-transform: uppercase;
    letter-spacing: 0.5px;
    line-height: 1.1;
    width: 150px;
  }
  .contact {
    position: absolute;
    left: 36px;
    bottom: 30px;
    color: var(--ink);
  }
  .person-name {
    color: var(--accent);
    font-weight: 800;
    font-size: 24px;
    letter-spacing: 1px;
    text-transform: uppercase;
    line-height: 1;
  }
  .person-title { font-size: 13px; margin-top: 3px; }
  .licence { font-size: 13px; margin-top: 14px; }
  .contact-list { list-style: none; margin-top: 12px; }
  .contact-list li {
    display: flex;
    align-items: center;
    gap: 8px;
    font-size: 12.5px;
    line-height: 1.7;
  }
  .contact-list svg { width: 12px; height: 12px; flex: none; }
  .edge-tab {
    position: absolute;
    left: 0;
    bottom: 60px;
    width: 16px;
    height: 22px;
    background: var(--accent);
  }
  .services {
    position: absolute;
    right: 28px;
    top: 38px;
    list-style: none;
    text-align: right;
    color: var(--ink-soft);
    font-size: 12px;
    line-height: 1.85;
  }
  .services li::after {
    content: "";
    display: inline-block;
    width: 5px; height: 5px;
    border-radius: 50%;
    background: var(--accent);
    margin-left: 7px;
    vertical-align: middle;
  }

  /* Logo side */
  .card-logo {
    display: flex;
    align-items: center;
    justify-content: center;
    gap: 14px;
  }
  .card-logo .brand-dot {
    width: 46px; height: 46px;
    background: var(--accent);
  }
  .card-logo .brand-name {
    color: var(--logo-muted);
    font-size: 26px;
    width: 260px;
  }
</style>
</head>
<body>

  <section class="card card-details">
    <div class="brand">
      <span class="brand-dot"></span>
      <span class="brand-name">Quandor Plumbing Solutions</span>
    </div>

    <ul class="services">
      <li>Emergency plumbing</li>
      <li>Plumbing maintenance</li>
      <li>Drainage maintenance</li>
      <li>Block sewer and stormwater</li>
      <li>Camera and locating</li>
    </ul>

    <span class="edge-tab"></span>

    <div class="contact">
      <p class="person-name">Felix</p>
      <p class="person-title">Founder &amp; CEO</p>
      <p class="licence">Licence number 728093K</p>
      <ul class="contact-list">
        <li>
          <svg viewBox="0 0 24 24" aria-hidden="true"><path fill="#4a90d9" d="M6.6 10.8a15.1 15.1 0 0 0 6.6 6.6l2.2-2.2a1 1 0 0 1 1-.25 11.4 11.4 0 0 0 3.6.57 1 1 0 0 1 1 1V20a1 1 0 0 1-1 1A17 17 0 0 1 3 4a1 1 0 0 1 1-1h3.5a1 1 0 0 1 1 1c0 1.25.2 2.45.57 3.57a1 1 0 0 1-.25 1z"/></svg>
          0461 539 207
        </li>
        <li>
          <svg viewBox="0 0 24 24" aria-hidden="true"><rect x="2" y="5" width="20" height="14" fill="#4a90d9"/><path d="M2 5l10 8 10-8" fill="none" stroke="#1f1f20" stroke-width="2"/></svg>
          quandorplumbingsolutions@mailbrook.example
        </li>
        <li>
          <svg viewBox="0 0 24 24" aria-hidden="true"><circle cx="12" cy="12" r="11" fill="#4a90d9"/></svg>
          @QuandorPlumbingSolutions
        </li>
      </ul>
    </div>
  </section>

  <section class="card card-logo">
    <span class="brand-dot"></span>
    <span class="brand-name">Quandor Plumbing Solutions</span>
  </section>

</body>
</html>
```